Business Card Design

We provide services doing multiple jobs in the construction industry.Please note: The company name needs to be ROCK SOLID BUILDING SERVICESAttached logo was an example of what we wanted. Can you change up the colors?

Industry/Entity Type

Construction

Contact Information for Business Card

ROCK SOLID BUILDING SERVICES5401 HUDSON BEND RDAUSTIN, TX 78734(512)243-6854ROCKSOLIDBUILDINGSERVICES@GMAIL.COM

```html
<!DOCTYPE html>
<html lang="en">
<head>
<meta charset="utf-8">
<title>Pearlwood Framing Works – Business Card</title>
<link href="https://fonts.googleapis.com/css2?family=Michroma&display=swap" rel="stylesheet">
<style>
  :root {
    --backdrop: #8e9193;
    --card: #ffffff;
    --navy: #1f1c5c;
    --navy-deep: #141244;
    --swoosh: #b9bcc2;
    --ink-light: #ffffff;
    --ink-soft: #d6d7ea;
  }
  * { margin: 0; padding: 0; box-sizing: border-box; }
  html, body {
    width: 1200px; height: 771px; overflow: hidden;
    background: var(--backdrop);
    font-family: "Michroma", sans-serif;
  }
  .stage {
    position: relative; width: 1200px; height: 771px;
    display: flex; align-items: center; justify-content: center; gap: 60px;
  }
  .card {
    position: relative; width: 520px; height: 297px;
    background: var(--card);
    box-shadow: 0 10px 24px rgba(0,0,0,.3);
    overflow: hidden;
  }
  .brand-name {
    color: var(--navy);
    font-size: 22px; line-height: 1.25; letter-spacing: 1px;
    text-align: center; text-transform: uppercase;
  }
  .card-front { display: flex; align-items: center; justify-content: center; }
  .card-back .band { position: absolute; inset: 0; }
  .card-back .brand-name {
    position: absolute; right: 14px; top: 104px; width: 158px;
    font-size: 14px; letter-spacing: .5px;
  }
  .contact {
    position: absolute; left: 14px; top: 104px;
    display: flex; gap: 10px; color: var(--ink-light);
  }
  .person { text-align: right; width: 128px; }
  .person-name { font-size: 9px; letter-spacing: .5px; white-space: nowrap; }
  .person-title { font-size: 6.5px; color: var(--ink-soft); margin-top: 5px; }
  .person-address {
    font-size: 6.5px; color: var(--ink-soft); margin-top: 16px;
    line-height: 1.8; white-space: nowrap;
  }
  .divider { width: 1px; background: var(--ink-soft); opacity: .7; }
  .details { list-style: none; font-size: 6.5px; line-height: 1.6; letter-spacing: .3px; }
  .details li {
    display: flex; align-items: flex-start; gap: 6px;
    white-space: nowrap; margin-bottom: 5px;
  }
  .details svg { flex: none; margin-top: 1.5px; }
</style>
</head>
<body>
<main class="stage">
  <section class="card card-front">
    <p class="brand-name">Pearlwood<br>Framing Works</p>
  </section>

  <section class="card card-back">
    <svg class="band" viewBox="0 0 520 297" aria-hidden="true">
      <defs>
        <linearGradient id="navyBand" x1="0" y1="0" x2="1" y2="0">
          <stop offset="0" stop-color="#141244"/>
          <stop offset="1" stop-color="#2a2672"/>
        </linearGradient>
      </defs>
      <path d="M0 0 H332 C358 70 292 150 328 297 H0 Z" fill="var(--swoosh)" transform="translate(14 0)"/>
      <path d="M0 0 H330 C356 70 290 150 326 297 H0 Z" fill="url(#navyBand)"/>
    </svg>

    <div class="contact">
      <div class="person">
        <p class="person-name">DANA WHITLOW</p>
        <p class="person-title">Owner / C.E.O</p>
        <p class="person-address">7732 FERNGLEN PASS LN<br>AUSTIN, TX 78700</p>
      </div>
      <div class="divider"></div>
      <ul class="details">
        <li><svg width="8" height="8" viewBox="0 0 8 8"><circle cx="4" cy="4" r="4" fill="#fff"/><path d="M2.6 2.2 3.3 3.4 2.9 3.9Q3.5 4.9 4.3 5.2L4.7 4.7 5.9 5.4 5.4 6.2Q3.1 5.8 1.8 3Z" fill="var(--navy)"/></svg><span>(512)555-0193</span></li>
        <li><svg width="8" height="8" viewBox="0 0 8 8"><circle cx="4" cy="4" r="4" fill="#fff"/><path d="M2.6 2.2 3.3 3.4 2.9 3.9Q3.5 4.9 4.3 5.2L4.7 4.7 5.9 5.4 5.4 6.2Q3.1 5.8 1.8 3Z" fill="var(--navy)"/></svg><span>(512)555-0148</span></li>
        <li><svg width="8" height="8" viewBox="0 0 8 8"><circle cx="4" cy="4" r="4" fill="#fff"/><path d="M2.6 2.2 3.3 3.4 2.9 3.9Q3.5 4.9 4.3 5.2L4.7 4.7 5.9 5.4 5.4 6.2Q3.1 5.8 1.8 3Z" fill="var(--navy)"/></svg><span>(512)555-0176</span></li>
        <li><svg width="8" height="8" viewBox="0 0 8 8"><circle cx="4" cy="4" r="4" fill="#fff"/><rect x="2" y="2.8" width="4" height="2.6" fill="none" stroke="var(--navy)" stroke-width=".6"/><path d="M2 2.8 4 4.3 6 2.8" fill="none" stroke="var(--navy)" stroke-width=".6"/></svg><span>PEARLWOODFRAMINGWORKS@<br>MAILNEST.EXAMPLE</span></li>
        <li><svg width="8" height="8" viewBox="0 0 8 8"><circle cx="4" cy="4" r="4" fill="#fff"/><circle cx="4" cy="4" r="2" fill="none" stroke="var(--navy)" stroke-width=".6"/><path d="M2 4H6M4 2V6" stroke="var(--navy)" stroke-width=".5"/></svg><span>WWW.PEARLWOOD.EXAMPLE</span></li>
      </ul>
    </div>

    <p class="brand-name">Pearlwood<br>Framing Works</p>
  </section>
</main>
</body>
</html>
```